Letterhead Design Project

Based on the attached logo we would like have a designed of stationary.
As we are a management consulting company focused on business development dealing with C-level and one level below we new business cards.
We have decided to use KMR (Kestrel Meridian Rowe) as the business name. The legal name will be Kestrel Meridian Rowe ApS but we will brand us under KMR. The tack line is “Shaping Lasting Gains” if we need one.
For legal reasons we need to have the legal name on the letters together with the company no. (cvr. nr. 58117904)
We want to signal the following:
- Serious
- Professional
- Creating Result
- Capable of thinking out of the box and creative
- Fast reactions we will be there when needed
What we do not want to be view as is:
- To smart
- We know better
- We can fix it yesterday
Our Value Proposition is two sited:
- Increasing revenue
- Reduced sales cost or increased efficiency
Therefore, companies can call us when they want to grow or they need to be more efficient.
Our business cards should have a two sided print with the logo incl. the tack line on one side and the detailed information on the other site.
We need to have the following information on the letter head:
- Legal company name
- Cvr nr.
- Address incl. country name (Denmark)
- Main number
- Wed address
Symbols are welcome to be used to guide for the above information.
The following information are expected to be in the personal signature of the letter.
- Name
- Title
- Mobile number
- E-mail address
Updates
Some of you has requested our specific details so here they come:
- Address incl. country name (Denmark): Lyngvænget 42, 3460 Birkerød, Denmark
- Main number: +45 7081 5532
- Wed address: www.kmrhalo.com
Mobile no. are +45 xxxx xxxx or +45 2287 3104
Our e-mail looks like this: firstname.seconname@KMRHALO.COM or for me: jonas.vallgren@kmrhalo.com
We need the design (file) as finish as posible so we just need to add personal details before printing.
Please be aware that we will prefer designs where we can print the full letter incl. design. As we are communicating on e-mails with pdf versions of the letter we also need to have a design which will print on the clients printers.
Target Market(s)
C level and one level below.
Major local and international Companies.
Industry/Entity Type
Management Consulting
Font styles to use
Colors
Designer to choose colors to be used in the design.
Requirements
Must have
- Use of our logo without tack line

```html
<!DOCTYPE html>
<html lang="en">
<head>
<meta charset="utf-8">
<title>KMR Letterhead</title>
<link rel="stylesheet" href="https://fonts.googleapis.com/css2?family=Quicksand:wght@500;600;700&display=swap">
<style>
  :root {
    --backdrop: #3b3b3b;
    --paper: #ffffff;
    --ink: #6d6d6d;
    --heading: #666666;
    --brand: #1565b8;
    --brand-deep: #0d4f9c;
    --brand-light: #2a86d6;
    --white: #ffffff;
  }
  * { box-sizing: border-box; margin: 0; padding: 0; }
  html, body {
    width: 1200px; height: 1000px; overflow: hidden;
    background: var(--backdrop);
    font-family: "Quicksand", sans-serif;
  }
  .letter {
    position: absolute; left: 268px; top: 11px;
    width: 687px; height: 970px;
    background: var(--paper);
  }
  .brand-mark {
    position: absolute; right: 40px; top: 42px;
    display: flex; align-items: center; gap: 10px;
    font-size: 52px; font-weight: 700; color: var(--brand);
    letter-spacing: 1px; line-height: 1;
  }
  .brand-mark .dot {
    width: 14px; height: 14px; border-radius: 50%;
    background: var(--brand);
  }
  .letter-body {
    position: absolute; left: 48px; top: 261px; width: 605px;
    color: var(--ink);
  }
  .letter-body h1 {
    font-size: 17px; font-weight: 700; color: var(--heading);
    line-height: 20px; margin-bottom: 14px;
  }
  .letter-body p {
    font-size: 12.4px; font-weight: 500; line-height: 11.3px;
    letter-spacing: -0.25px; word-spacing: -0.5px;
    text-align: justify; hyphens: auto;
    margin-bottom: 16px;
  }
  .sign-off {
    position: absolute; left: 48px; top: 779px;
    color: var(--brand);
  }
  .signature {
    width: 92px; height: 28px; border-radius: 3px;
    background: linear-gradient(90deg, #dfe6f3, #c9d4ea);
    margin-bottom: 6px;
  }
  .sign-off .name { font-size: 12.5px; font-weight: 700; line-height: 16px; }
  .sign-off .title { font-size: 10.5px; font-weight: 500; line-height: 13px; margin-bottom: 7px; }
  .sign-off .contact { font-size: 10.5px; font-weight: 500; line-height: 13.5px; }
  .company-bar {
    position: absolute; left: 17px; top: 921px;
    width: 652px; height: 29px;
    background: linear-gradient(90deg, var(--brand-deep), var(--brand-light) 50%, var(--brand-deep));
    color: var(--white);
    display: flex; align-items: center; justify-content: space-between;
    padding: 0 6px;
    font-size: 9.3px; font-weight: 600; white-space: nowrap;
  }
  .company-bar .item { display: flex; align-items: center; gap: 6px; }
  .company-bar svg { width: 14px; height: 14px; flex: none; }
</style>
</head>
<body>
  <main class="letter">
    <div class="brand-mark"><span class="dot"></span>KMR</div>

    <section class="letter-body">
      <h1>Sample Text</h1>
      <p>Lorem ipsum dolor sit amet, consectetur adipiscing elit. Pellentesque ornare enim a tristique aliquet. Aliquam congue, urna at ultrices venenatis, dolor diam ultricies felis, sed placerat ante lacus dignissim mi. Integer a suscipit erat, at vestibulum arcu. Nulla blandit lectus augue, sed dapibus lorem laoreet nec. Donec nulla nisl, rutrum eu tincidunt id, pharetra vitae metus. Cum sociis natoque penatibus et magnis dis parturient montes, nascetur ridiculus mus. Pellentesque feugiat pulvinar tortor, eu fermentum tellus elementum id.</p>
      <p>Duis sit amet velit mi. Sed accumsan lacus non lacus imperdiet congue. Morbi ac sapien sed urna ornare venenatis eget sed diam. Duis turpis risus, ullamcorper ut arcu non, suscipit adipiscing leo. Etiam auctor aliquam luctus. Aenean vestibulum sapien nec enim aliquam accumsan. Integer fringilla ac augue fringilla hendrerit. Sed porttitor sollicitudin sem, ut laoreet metus volutpat ut.</p>
      <p>Nulla venenatis nibh vel mattis accumsan. Proin consectetur adipiscing dui ac convallis. Praesent vitae est dignissim, pretium nulla non, eleifend velit. Maecenas pulvinar, nisl at venenatis placerat, felis leo scelerisque mauris, vel luctus magna massa nec lorem. Sed sed lorem lectus. Fusce suscipit turpis vitae neque eleifend mattis. Etiam hendrerit vitae ligula et elementum. Nunc quis lobortis lacus. Integer eleifend quam dolor, et pulvinar lectus sodales eget. Quisque ultricies arcu quis vulputate accumsan.</p>
      <p>Lorem ipsum dolor sit amet, consectetur adipiscing elit. Pellentesque ornare enim a tristique aliquet. Aliquam congue, urna at ultrices venenatis, dolor diam ultricies felis, sed placerat ante lacus dignissim mi. Integer a suscipit erat, at vestibulum arcu. Nulla blandit lectus augue, sed dapibus lorem laoreet nec. Donec nulla nisl, rutrum eu tincidunt id, pharetra vitae metus. Cum sociis natoque penatibus et magnis dis parturient montes, nascetur ridiculus mus. Pellentesque feugiat pulvinar tortor, eu fermentum tellus elementum id.</p>
      <p>Duis sit amet velit mi. Sed accumsan lacus non lacus imperdiet congue. Morbi ac sapien sed urna ornare venenatis eget sed diam. Duis turpis risus, ullamcorper ut arcu non, suscipit adipiscing leo. Etiam auctor aliquam luctus. Aenean vestibulum sapien nec enim aliquam accumsan. Integer fringilla ac augue fringilla hendrerit. Sed porttitor sollicitudin sem, ut laoreet metus volutpat ut.</p>
    </section>

    <section class="sign-off">
      <div class="signature" role="img" aria-label="Handwritten signature of Mikkel R"></div>
      <div class="name">Mikkel Ravnholt</div>
      <div class="title">Title</div>
      <div class="contact">Mobil/direct: +45 xxxx xxxx</div>
      <div class="contact">E-mail: xxxxxx.xxxxxx@kmrhalo.com</div>
    </section>

    <footer class="company-bar">
      <span class="item">Kestrel Meridian Rowe ApS, CVR: 58 11 79 04</span>
      <span class="item">
        <svg viewBox="0 0 14 14" fill="none" stroke="#fff" stroke-width="1"><circle cx="7" cy="7" r="6.3"/><path d="M7 11 C5 8.5 4.6 7.4 4.6 6.2 a2.4 2.4 0 0 1 4.8 0 c0 1.2-.4 2.3-2.4 4.8z"/><circle cx="7" cy="6.2" r=".8" fill="#fff"/></svg>
        Lyngvænget 42, 4795 Halmstrup, Denmark
      </span>
      <span class="item">
        <svg viewBox="0 0 14 14" fill="none" stroke="#fff" stroke-width="1"><circle cx="7" cy="7" r="6.3"/><path d="M4.8 4.2 l1.2-.4 .8 1.6-.7.6 c.4.9 1 1.5 1.9 1.9 l.6-.7 1.6.8-.4 1.2 c-2.8.2-5.2-2.2-5-5z" fill="#fff" stroke="none"/></svg>
        +45 7081 5532
      </span>
      <span class="item">
        <svg viewBox="0 0 14 14" fill="none" stroke="#fff" stroke-width="1"><circle cx="7" cy="7" r="6.3"/><ellipse cx="7" cy="7" rx="2.6" ry="6.3"/><path d="M.7 7h12.6M1.8 3.8h10.4M1.8 10.2h10.4"/></svg>
        www.kmrhalo.com
      </span>
    </footer>
  </main>
</body>
</html>
```